Brookvane Consulting Business Card Design

Business Card Design for Brookvane Consulting. Brookvane Consulting is a boutique consultancy based in Atlanta, GA., that specializes in marketing strategy, organization planning, and leadership development. We provide solutions for small businesses and startups as well as Vantage 300 companies.

http://brookvaneconsulting.com/

Target Market(s)

We provide solutions for small businesses and startups as well as Vantage 300 companies.

Industry/Entity Type

Consulting

Contact Information for Business Card

Two sided business card with priority on contact information, logo, tag line (Inspiration to Dream More, Do More, Become More)

Colors

Designer to choose colors to be used in the design.

Requirements
Must have
• contact information, logo, tag line (Inspiration to Dream More, Do More, Become More)
• Simple no over communication.
Nice to have
• I would like to see different placements of logo and creative use of both sides of the card
Should not have
• Do not put too much information on the card.

```html
<!DOCTYPE html>
<html lang="en">
<head>
<meta charset="utf-8">
<title>Brookvane Consulting Business Card</title>
<link href="https://fonts.googleapis.com/css2?family=Lato:wght@400;700&display=swap" rel="stylesheet">
<style>
  :root {
    --backdrop: #999999;
    --card-light: #ffffff;
    --card-dark: #333333;
    --ink: #2b2b2b;
    --ink-soft: #3a3a3a;
    --rule: #9a9a9a;
    --paper-text: #ffffff;
  }
  html, body {
    margin: 0;
    padding: 0;
    width: 1200px;
    height: 900px;
    overflow: hidden;
    background: var(--backdrop);
    font-family: "Lato", sans-serif;
  }
  .stage {
    position: relative;
    width: 1200px;
    height: 900px;
  }
  .card {
    position: absolute;
    top: 306px;
    height: 271px;
    border-radius: 10px;
    box-shadow: 0 2px 4px rgba(0,0,0,0.35);
  }
  .card-front {
    left: 149px;
    width: 438px;
    background: var(--card-light);
    color: var(--ink);
  }
  .card-back {
    left: 609px;
    width: 441px;
    background: var(--card-dark);
    color: var(--paper-text);
  }
  .front-brand {
    position: absolute;
    right: 30px;
    top: 86px;
    margin: 0;
    font-size: 22px;
    font-weight: 400;
    letter-spacing: 0.5px;
    color: var(--ink);
    white-space: nowrap;
  }
  .holder {
    position: absolute;
    left: 24px;
    top: 164px;
  }
  .holder-name {
    margin: 0;
    font-size: 16px;
    font-weight: 700;
    line-height: 18px;
    color: var(--ink);
  }
  .holder-title {
    margin: 0;
    font-size: 12.5px;
    line-height: 15px;
    color: var(--ink-soft);
  }
  .divider {
    position: absolute;
    left: 132px;
    top: 191px;
    width: 284px;
    height: 1px;
    background: var(--rule);
  }
  .contact-list {
    position: absolute;
    right: 23px;
    top: 205px;
    margin: 0;
    padding: 0;
    list-style: none;
    text-align: right;
  }
  .contact-item {
    display: flex;
    justify-content: flex-end;
    align-items: center;
    gap: 3px;
    font-size: 13px;
    line-height: 16.5px;
    color: var(--ink);
  }
  .contact-icon {
    width: 9px;
    height: 9px;
    fill: var(--ink);
  }
  .back-brand {
    position: absolute;
    left: 0;
    right: 0;
    top: 112px;
    margin: 0;
    text-align: center;
    font-size: 34px;
    font-weight: 400;
    letter-spacing: 0.5px;
    color: var(--paper-text);
  }
  .tagline {
    position: absolute;
    left: 0;
    right: 0;
    top: 225px;
    margin: 0;
    text-align: center;
    font-size: 11.5px;
    font-weight: 700;
    color: var(--paper-text);
    text-transform: uppercase;
  }
</style>
</head>
<body>
<main class="stage">
  <section class="card card-front" aria-label="Card front">
    <p class="front-brand">Brookvane Consulting</p>
    <div class="holder">
      <p class="holder-name">DANIEL MORROW</p>
      <p class="holder-title">Managing Director</p>
    </div>
    <div class="divider"></div>
    <ul class="contact-list">
      <li class="contact-item">444 555 7120
        <svg class="contact-icon" viewBox="0 0 10 10" aria-hidden="true"><path d="M1 3 Q5 0 9 3 L8 4.3 L6.6 3.6 L6.6 2.8 Q5 2.3 3.4 2.8 L3.4 3.6 L2 4.3 Z M2.5 5 H7.5 L8.5 9 H1.5 Z"/></svg>
      </li>
      <li class="contact-item">info@brookvaneconsulting.com
        <svg class="contact-icon" viewBox="0 0 10 10" aria-hidden="true"><path d="M0.5 2 H9.5 V8 H0.5 Z M1.3 2.6 L5 5.4 L8.7 2.6" stroke="#fff" stroke-width="0.7"/></svg>
      </li>
      <li class="contact-item">www.brookvaneconsulting.com
        <svg class="contact-icon" viewBox="0 0 10 10" aria-hidden="true"><circle cx="5" cy="5" r="4.5"/><path d="M3 3 Q5 2 6 4 Q4 5 3.5 7 Q2 5 3 3 Z M6.5 6 Q7.8 6.2 7.5 7.5 Q6.5 7.8 6.5 6 Z" fill="#fff"/></svg>
      </li>
    </ul>
  </section>

  <section class="card card-back" aria-label="Card back">
    <p class="back-brand">Brookvane Consulting</p>
    <p class="tagline">Inspiration to Dream More, Do More, Become More</p>
  </section>
</main>
</body>
</html>
```